Business Card Design Project

After recently finishing a design project for the company logo using markbazaar, it's now time for a business card. Attached to this is the logo.

The requirements for the business card are pretty straightforward:

- A clean, uncomplicated look
- Consistent usage of fonts
- Designs for both single sided and double sided cards
- A modern layout with preferably space to refer to social media accounts and/or downloadable vcards through a qr code
- consistent application of the company colour scheme: red/white. Hex codes for exact colour can be provided

Thanks!

```html
<!DOCTYPE html>
<html lang="en">
<head>
<meta charset="utf-8">
<title>Northgate Staffing – Business Card</title>
<link rel="stylesheet" href="https://fonts.googleapis.com/css2?family=Source+Sans+3:wght@400;600;700&display=swap">
<style>
  :root {
    --brand-red: #e31e24;
    --ink: #231f20;
    --ink-soft: #2b2b2b;
    --card: #ffffff;
    --backdrop: #ece9e6;
    --block-dark: #231f20;
  }
  html, body {
    margin: 0;
    padding: 0;
    width: 960px;
    height: 1200px;
    overflow: hidden;
    background: var(--backdrop);
    font-family: "Source Sans 3", "Myriad Pro", Arial, sans-serif;
  }
  .canvas {
    position: relative;
    width: 960px;
    height: 1200px;
  }
  .card {
    position: absolute;
    width: 840px;
    height: 480px;
    background: var(--card);
    border-radius: 30px;
    overflow: hidden;
    box-shadow: 0 2px 6px rgba(0,0,0,0.12);
  }
  .card--front { left: 55px; top: 92px; }
  .card--back  { left: 60px; top: 637px; }

  .brand {
    position: absolute;
    display: flex;
    align-items: center;
    gap: 22px;
    white-space: nowrap;
  }
  .brand__square {
    display: block;
    background: var(--brand-red);
  }
  .brand__name {
    font-weight: 600;
    line-height: 1;
    letter-spacing: -0.5px;
  }
  .card--front .brand {
    left: 0; right: 0;
    top: 96px;
    justify-content: center;
  }
  .card--front .brand__square { width: 64px; height: 64px; }
  .card--front .brand__name { font-size: 70px; color: var(--ink); }

  .name-band {
    position: absolute;
    left: 0;
    top: 256px;
    width: 721px;
    height: 58px;
    background: var(--brand-red);
    color: #fff;
    display: flex;
    align-items: center;
    justify-content: center;
    padding-left: 30px;
    box-sizing: border-box;
  }
  .name-band__name { font-weight: 700; font-size: 26px; }
  .name-band__role { font-weight: 400; font-size: 20px; margin-left: 6px; }
  .end-block {
    position: absolute;
    left: 731px;
    top: 256px;
    width: 109px;
    height: 58px;
    background: var(--block-dark);
  }

  .contact {
    position: absolute;
    left: 67px;
    top: 362px;
    margin: 0;
    padding: 0;
    list-style: none;
    font-size: 20px;
    color: var(--ink-soft);
    line-height: 35px;
  }
  .contact__label { font-weight: 700; font-style: italic; }
  .address {
    position: absolute;
    left: 447px;
    top: 406px;
    font-style: normal;
    font-size: 20px;
    color: var(--ink-soft);
    line-height: 28px;
  }

  .card--back .brand {
    left: 0; right: 0;
    top: 205px;
    justify-content: center;
  }
  .card--back .brand__square { width: 72px; height: 72px; }
  .card--back .brand__name { font-size: 72px; color: var(--brand-red); }
</style>
</head>
<body>
<main class="canvas">
  <section class="card card--front" aria-label="Business card front">
    <div class="brand">
      <span class="brand__square" aria-hidden="true"></span>
      <span class="brand__name">Northgate Staffing</span>
    </div>
    <div class="name-band">
      <span class="name-band__name">Your Name -</span>
      <span class="name-band__role">Designation</span>
    </div>
    <div class="end-block" aria-hidden="true"></div>
    <ul class="contact">
      <li><span class="contact__label">t</span> : 123-123-1234</li>
      <li><span class="contact__label">e</span> : info@yourwebsite.com</li>
      <li><span class="contact__label">w</span> : www.northgatestaffing.com</li>
    </ul>
    <address class="address">
      1234, Street Name<br>
      District, City, Country Code.
    </address>
  </section>

  <section class="card card--back" aria-label="Business card back">
    <div class="brand">
      <span class="brand__square" aria-hidden="true"></span>
      <span class="brand__name">Northgate</span>
    </div>
  </section>
</main>
</body>
</html>
```